Flyer design for growing electrical business!!!

looking to get some flyers made for advertising to spread the word about my new business to hopefully create more work!
i am letting potential clients know the type of work i do and am trying to sell my services to them.
To be put on double sided A5. the attached document file has what i would like on each page.
i would like my logo on the first page and and colour scheme of black orange and silver for the flyer following the colours of my logo.
On the second page i would like the photo as a focal point on the top half.
The bold writing are my selling points and would like them accentuated.
Industry/Entity Type
Advertising
Look and feel
Each slider illustrates characteristics of the customer's brand and the style your logo design should communicate.

```html
<!DOCTYPE html>
<html lang="en">
<head>
<meta charset="utf-8">
<title>Kestrel Power Electrical – Flyer</title>
<link href="https://fonts.googleapis.com/css2?family=Oswald:wght@500;700&family=Roboto+Condensed:wght@400;700&family=Arimo:wght@400;700&display=swap" rel="stylesheet">
<style>
:root{
  --orange:#ec5a24;
  --yellow:#ffd400;
  --dark:#262626;
  --dark-2:#3a3a3a;
  --silver:#e6e6e6;
  --grey:#9a9a9a;
  --ink:#1e1e1e;
  --white:#ffffff;
  --row-alt:#ececec;
}
*{margin:0;padding:0;box-sizing:border-box}
html,body{width:1200px;height:1000px;overflow:hidden;background:var(--white)}
body{position:relative;font-family:"Arimo",Arial,sans-serif}
.page{position:absolute;top:120px;width:532px;height:746px;overflow:hidden}
.page--front{left:54px;background:var(--white)}
.page--back{left:614px;background:linear-gradient(180deg,var(--dark-2),var(--dark))}
.abs{position:absolute}

/* FRONT */
.front-panel{position:absolute;left:0;top:0}
.headline{left:34px;top:22px;font-family:"Oswald",sans-serif;font-weight:700;font-size:45px;line-height:44px;color:var(--orange);letter-spacing:.5px}
.headline .light{color:var(--silver)}
.quote-tag{left:345px;top:60px;width:230px;transform:rotate(45deg);transform-origin:center;text-align:center;font-family:"Oswald",sans-serif;font-weight:700;color:var(--ink);line-height:1}
.quote-tag .l1{font-size:22px}
.quote-tag .l2{font-size:36px}
.quote-tag .l3{font-size:20px}
.quote-tag .l3 b{color:var(--yellow)}
.quote-tag .l4{font-size:16px}
.needs-bar{left:0;top:165px;width:348px;height:27px;background:var(--orange);color:var(--white);font-family:"Arimo",sans-serif;font-weight:700;font-size:14.5px;line-height:27px;padding-left:33px}
.needs-bar svg{position:absolute;right:-4px;top:3px}
.service-types{left:34px;top:211px;color:var(--white);font-weight:700;font-size:16.5px;line-height:20px;letter-spacing:.3px}
.service-list{list-style:none;font-family:"Roboto Condensed",sans-serif;font-size:18px;color:var(--white);line-height:29.5px}
.service-list li{position:relative;padding-left:20px}
.service-list li::before{content:"";position:absolute;left:0;top:11px;width:13px;height:7px;background:var(--orange);border-radius:4px 1px 1px 4px}
.service-list .wrap{line-height:23px;padding-bottom:6px}
.list-a{left:34px;top:268px}
.list-b{left:258px;top:268px}
.brand-name{left:30px;top:640px;width:200px;font-family:"Oswald",sans-serif;font-weight:700;font-size:22px;color:var(--orange);display:flex;align-items:center;gap:8px}
.brand-name .dot{width:14px;height:14px;border-radius:50%;background:var(--orange)}
.contact{left:221px;top:586px;width:300px;color:var(--ink)}
.contact .name{font-family:"Oswald",sans-serif;font-weight:700;font-size:17px}
.contact .phone{font-family:"Oswald",sans-serif;font-weight:700;font-size:27px;color:var(--orange);line-height:32px}
.contact .email{font-size:14.5px;padding-bottom:8px;border-bottom:1px solid #c8c8c8;width:260px}
.contact .reg{font-size:13px;margin-top:8px}
.contact .note{font-size:11.5px;line-height:14px;margin-top:2px}

/* BACK */
.photo{left:0;top:0}
.back-brand{left:418px;top:266px;font-family:"Oswald",sans-serif;font-weight:700;font-size:13px;color:var(--orange);display:flex;align-items:center;gap:5px}
.back-brand .dot{width:9px;height:9px;border-radius:50%;background:var(--orange)}
.q{font-weight:700;font-size:14px;line-height:16px}
.q--orange{left:27px;top:333px;color:var(--orange)}
.q--white{left:27px;top:374px;color:var(--white)}
.divider{left:278px;top:335px;width:1px;height:64px;background:var(--grey)}
.saving{left:294px;top:328px;color:var(--white);font-weight:700}
.saving .s1{font-size:21px;line-height:24px}
.saving .s2{font-size:37px;line-height:36px;color:var(--orange)}
.saving .s3{font-size:15px;line-height:17px}
.basis{left:27px;top:414px;color:var(--orange);font-family:"Roboto Condensed",sans-serif;font-weight:700;font-size:15.5px}
.body-copy{left:27px;top:437px;width:480px;color:var(--white);font-size:14px;line-height:17px}
.table-title{left:27px;color:var(--white);font-family:"Roboto Condensed",sans-serif;font-weight:700;font-size:16px}
.t1{top:480px}.t2{top:585px}
table{position:absolute;left:27px;width:475px;border-collapse:collapse;font-size:9px;text-align:center;color:var(--ink)}
table.tab1{top:504px}table.tab2{top:610px}
th{background:var(--orange);color:var(--white);font-weight:700;height:14px;border-right:1px solid var(--white)}
td{background:var(--white);height:12.5px;border-right:1px solid #bbb;font-weight:700}
tr:nth-child(even) td{background:var(--row-alt)}
.led-note{left:27px;top:695px;color:var(--orange);font-weight:700;font-size:11.5px}
.led-types{left:27px;top:709px;color:var(--white);font-size:11.5px}
.led-types span{margin-right:6px}
.led-types span::before{content:"▸ ";color:var(--orange)}
</style>
</head>
<body>

<section class="page page--front">
  <svg class="front-panel" width="532" height="746" viewBox="0 0 532 746">
    <defs>
      <linearGradient id="brushed" x1="0" y1="0" x2="0" y2="1">
        <stop offset="0" stop-color="#3b3b3b"/><stop offset="1" stop-color="#262626"/>
      </linearGradient>
    </defs>
    <polygon points="0,0 532,0 532,430 370,552 0,552" fill="url(#brushed)"/>
    <polygon points="0,552 370,552 532,430 532,440 374,559 0,559" fill="#ec5a24"/>
    <polygon points="277,0 532,0 532,242" fill="#ec5a24"/>
  </svg>

  <h1 class="abs headline">LOCAL<br>ELECTRICIAN<br><span class="light">IN YOUR AREA</span></h1>

  <div class="abs quote-tag">
    <div class="l1">CALL</div>
    <div class="l2">TODAY</div>
    <div class="l3">FOR A <b>FREE</b></div>
    <div class="l4">NO OBLIGATION QUOTE</div>
  </div>

  <div class="abs needs-bar">FOR ALL YOUR ELECTRICAL NEEDS
    <svg width="30" height="22" viewBox="0 0 30 22"><rect x="4" y="5" width="12" height="12" rx="3" fill="#fff"/><rect x="16" y="7" width="8" height="2.5" fill="#fff"/><rect x="16" y="12.5" width="8" height="2.5" fill="#fff"/><rect x="0" y="9.5" width="5" height="3" fill="#fff"/></svg>
  </div>

  <p class="abs service-types">NEW INSTALLATIONS - RENOVATIONS<br>ADDITIONS – UPGRADES – REPAIRS – MAINTENANCE</p>

  <ul class="abs service-list list-a">
    <li>Lighting</li><li>LED lighting</li><li>Garden lighting</li><li>Ceiling fans</li><li>Dimmers</li><li>Smoke detectors</li><li>Power points</li><li>Ovens and Cooktops</li><li>Telephone</li>
  </ul>
  <ul class="abs service-list list-b">
    <li>Data</li><li>TV/Aerial</li><li>Switchboard upgrades</li><li class="wrap">Safety switches (RCDS)<br>and Circuit breakers</li><li>Surge protectors</li><li>Hot Water Units</li><li>Test tagging</li>
  </ul>

  <div class="abs brand-name"><span class="dot"></span>KESTREL POWER</div>

  <div class="abs contact">
    <div class="name">SAM CARTER</div>
    <div class="phone">0400 123 456</div>
    <div class="email">kestrelpower@example.com</div>
    <div class="reg">ABN 12 345 678 901 &nbsp; Lic 123456C</div>
    <div class="note">At Kestrel Power we are fully insured and all work is<br>completed to current Australian Electrical Standards</div>
  </div>
</section>

<section class="page page--back">
  <svg class="photo" width="532" height="310" viewBox="0 0 532 310">
    <defs>
      <linearGradient id="kitchen" x1="0" y1="0" x2="0" y2="1">
        <stop offset="0" stop-color="#e9e6e0"/><stop offset=".6" stop-color="#cfcac2"/><stop offset="1" stop-color="#6c655d"/>
      </linearGradient>
    </defs>
    <polygon role="img" aria-label="Photo of a modern white kitchen with marble island bench and bar stools" points="0,0 532,0 532,178 325,300 0,300" fill="url(#kitchen)"/>
    <polygon points="325,300 532,178 532,186 330,306 0,306 0,300" fill="#ec5a24"/>
  </svg>
  <div class="abs back-brand"><span class="dot"></span>KESTREL POWER</div>

  <p class="abs q q--orange">ARE YOU SPENDING TOO MUCH<br>ON YOUR ELECTRICITY BILL?</p>
  <p class="abs q q--white">ARE YOU SICK AND TIRED OF<br>CHANGING GLOBES?</p>
  <div class="abs divider"></div>
  <div class="abs saving">
    <div class="s1">SAVE UP TO</div>
    <div class="s2">$500 OFF</div>
    <div class="s3">YOUR ELECTRICITY BILL</div>
  </div>
  <p class="abs basis">BASED ON CHANGING JUST 22 OF YOUR HALOGEN DOWNLIGHTS TO LED</p>
  <p class="abs body-copy">Why not save yourself some money while adding value to your house!<br>LEDs use at least 75% less electricity and last up to 50 times longer</p>

  <h2 class="abs table-title t1">YEARLY PRICES BASED ON 6 HOURS USE PER DAY @ $0.26 per kWh</h2>
  <table class="tab1">
    <tr><th>NUMBER OF DOWNLIGHTS</th><th>HALOGEN GLOBE(50W)</th><th>LED (10W)</th><th>SAVINGS</th></tr>
    <tr><td>1</td><td>$28.47 per year</td><td>$5.69 per year</td><td>$22.78 per year</td></tr>
    <tr><td>10</td><td>$284.70</td><td>$56.90</td><td>$227.80</td></tr>
    <tr><td>20</td><td>$569.40</td><td>$113.80</td><td>$455.60</td></tr>
    <tr><td>30</td><td>$854.10</td><td>$170.70</td><td>$683.40</td></tr>
  </table>

  <h2 class="abs table-title t2">YEARLY REPLACEMENT COSTS BASED ON 6 HOURS USE PER DAY</h2>
  <table class="tab2">
    <tr><th>NUMBER OF DOWNLIGHTS</th><th>HALOGEN GLOBE(50W)</th><th>LED (10W)</th></tr>
    <tr><td>1</td><td>$28.47 per year</td><td>$5.69 per year</td></tr>
    <tr><td>10</td><td>$284.70</td><td>$56.90</td></tr>
    <tr><td>20</td><td>$569.40</td><td>$113.80</td></tr>
    <tr><td>30</td><td>$854.10</td><td>$170.70</td></tr>
  </table>

  <p class="abs led-note">Not just downlights, you can change any light to LED</p>
  <p class="abs led-types"><span>Oyster lights</span><span>Directional lights</span><span>Spot lights</span><span>Wall lights</span><span>Pendant lights</span><span>External lights</span></p>
</section>

</body>
</html>
```